My project benefits Military, First Responders, Police, Fire, and Educators.

Contact Information for Business Card

2 Sided appointment card. Visual side will have my head shot with "Brisk Lantern" in a bold graffic/text. I am picturing maybe the headshot applied to a filter that has a matrix effect where the picture is made up of data/numbers flowing vertically through the photo. I am of course open to other concepts as well. Side two will have contact info presented in an attractive visual complimenting the front.

```html
<!DOCTYPE html>
<html lang="en">
<head>
<meta charset="utf-8">
<title>Brisk Lantern – Business Card</title>
<link rel="stylesheet" href="https://fonts.googleapis.com/css2?family=Orbitron:wght@500;700;900&family=Saira+Condensed:wght@300&display=swap">
<style>
  :root {
    --stage: #4b4b4b;
    --card: #000000;
    --neon: #8fd43a;
    --code-green: #1f6b1a;
    --code-deep: #0a2a08;
  }
  html, body {
    margin: 0;
    width: 1200px;
    height: 1200px;
    overflow: hidden;
    background: var(--stage);
  }
  .stage {
    position: relative;
    width: 1200px;
    height: 1200px;
  }
  .card {
    position: absolute;
    top: 239px;
    width: 411px;
    height: 721px;
    background: var(--card);
    overflow: hidden;
  }
  .card--contact { left: 166px; }
  .card--portrait { left: 626px; }
  .code-rain {
    position: absolute;
    left: 0; top: 0;
    width: 100%;
    height: 400px;
    background: linear-gradient(180deg, var(--code-deep) 0%, #0d3a0b 45%, #061c05 75%, var(--card) 100%);
  }
  .portrait-area {
    position: absolute;
    left: 0; top: 0;
    width: 100%;
    height: 630px;
    background:
      radial-gradient(ellipse 45% 40% at 62% 35%, #3f8f2c 0%, transparent 70%),
      linear-gradient(180deg, #163f12 0%, #0f3a0c 55%, #071d06 85%, var(--card) 100%);
  }
  .card-art {
    position: absolute;
    inset: 0;
    width: 100%;
    height: 100%;
  }
  .trace { fill: none; stroke: var(--neon); stroke-width: 2; }
  .node { fill: var(--neon); }
  .name { font-family: "Orbitron", sans-serif; font-weight: 700; font-size: 38px; fill: var(--neon); }
  .contact { font-family: "Orbitron", sans-serif; font-weight: 500; fill: var(--neon); }
  .phone { font-size: 25px; }
  .email, .web { font-size: 21px; }
  .audience { font-family: "Orbitron", sans-serif; font-weight: 500; font-size: 25px; fill: var(--neon); }
  .experience { font-family: "Saira Condensed", sans-serif; font-weight: 300; font-size: 24px; fill: var(--neon); }
  .brand { font-family: "Orbitron", sans-serif; font-weight: 900; font-size: 40px; fill: var(--neon); }
</style>
</head>
<body>
<main class="stage">

  <section class="card card--contact">
    <div class="code-rain" role="img" aria-label="Falling green digital code columns"></div>
    <svg class="card-art" viewBox="0 0 514 901" xmlns="http://www.w3.org/2000/svg">
      <text class="name" x="113" y="291">DANA HOLLIS</text>
      <polyline class="trace" points="0,336 436,336 436,277"/>
      <circle class="node" cx="436" cy="277" r="7"/>
      <polyline class="trace" points="288,336 288,382 457,382 457,466 97,466"/>
      <circle class="node" cx="97" cy="466" r="7"/>
      <polyline class="trace" points="0,363 208,363 208,423"/>
      <circle class="node" cx="208" cy="423" r="7"/>
      <polyline class="trace" points="38,363 38,546 258,546 258,574"/>
      <circle class="node" cx="258" cy="574" r="7"/>

      <text class="contact phone" x="231" y="434">(0) 000-000</text>
      <text class="contact email" x="98" y="509">DANA@BRISKLANTERN.COM</text>
      <text class="contact web" x="130" y="614">BRISKLANTERN.COM</text>

      <g class="crosshair" fill="none" stroke="var(--neon)" stroke-width="2">
        <circle cx="109" cy="728" r="55"/>
        <circle cx="109" cy="728" r="45"/>
        <line x1="29" y1="728" x2="189" y2="728"/>
        <line x1="109" y1="648" x2="109" y2="808"/>
      </g>
      <text class="audience" x="190" y="684">Military,</text>
      <text class="audience" x="190" y="718">Law Enforcement,</text>
      <text class="audience" x="190" y="753">First Responders,</text>
      <text class="audience" x="190" y="787">&amp; Educators.</text>

      <text class="experience" x="257" y="868" text-anchor="middle">14 years of experience</text>
    </svg>
  </section>

  <section class="card card--portrait">
    <div class="portrait-area" role="img" aria-label="Headshot of a smiling man in suit and tie, rendered through a green falling-code filter"></div>
    <svg class="card-art" viewBox="0 0 514 901" xmlns="http://www.w3.org/2000/svg">
      <text class="brand" x="257" y="809" text-anchor="middle">BRISK LANTERN</text>
    </svg>
  </section>

</main>
</body>
</html>
```